Business Card for: Bramwell Financial Advisory Services Inc.

provide strategic financial advisory services to companies in the areas of corporate finance, mergers and acquisitions, executive coaching and strategic planning

Target Market(s)

Companies, banks, accountants, lawyers

Industry/Entity Type

High end business consulting in corporate finance, mergers and acquisitions, consulting

Contact Information for Business Card

Name of company, Name: xxxxxx xxxxxx , CEO, - phone number: 1-xxx-xxx-xxxx, - email address,

Requirements
Must have
• Must be professional and simple.
Nice to have
• simple, straight graphics, must give the impression that we are trustworthy, professional, competent
Should not have
• loud colors, loud design features

```html
<!DOCTYPE html>
<html lang="en">
<head>
<meta charset="utf-8">
<title>Bramwell Financial Advisory Services Inc. – Business Card</title>
<link rel="stylesheet" href="https://fonts.googleapis.com/css2?family=Poppins:wght@400;500;600;700&display=swap">
<style>
  :root {
    --navy: #07456f;
    --gold: #a8843c;
    --white: #ffffff;
    --backdrop: #1c1c1c;
  }
  * { margin: 0; padding: 0; box-sizing: border-box; }
  html, body {
    width: 1200px;
    height: 741px;
    overflow: hidden;
    background: var(--backdrop);
    font-family: "Poppins", sans-serif;
  }
  .stage { position: relative; width: 1200px; height: 741px; }
  .card {
    position: absolute;
    top: 215px;
    width: 478px;
    height: 280px;
    border-radius: 20px;
    overflow: hidden;
    background: var(--white);
  }
  .card--front { left: 112px; }
  .card--back { left: 613px; }
  .card__art { position: absolute; inset: 0; width: 100%; height: 100%; }

  .brand { position: absolute; color: var(--navy); font-weight: 600; line-height: 1; }
  .brand__name { display: block; font-size: 34px; letter-spacing: 0.5px; }
  .brand__tagline { display: block; font-size: 10.5px; font-weight: 500; margin-top: 6px; letter-spacing: 0.2px; }
  .card--front .brand { left: 30px; top: 40px; }
  .card--back .brand { left: 30px; top: 92px; }

  .contact { position: absolute; left: 281px; top: 121px; color: var(--white); white-space: nowrap; }
  .contact__name { font-size: 16px; font-weight: 700; line-height: 18px; letter-spacing: 0.2px; }
  .contact__role { font-size: 11px; color: var(--gold); font-weight: 400; line-height: 13px; }
  .contact__address { margin-top: 9px; font-size: 12px; line-height: 17px; }
  .contact__lines { margin-top: 5px; font-size: 12px; line-height: 18px; list-style: none; }
  .contact__lines li { display: flex; align-items: center; gap: 6px; }
  .contact__icon { width: 13px; height: 13px; flex: none; }

  .website {
    position: absolute;
    right: 16px;
    bottom: 24px;
    color: var(--white);
    font-size: 12px;
  }
</style>
</head>
<body>
<main class="stage">

  <section class="card card--front" aria-label="Business card front">
    <svg class="card__art" viewBox="0 0 478 280" aria-hidden="true">
      <ellipse cx="375" cy="165" rx="265" ry="118" transform="rotate(-22 375 165)" fill="var(--gold)"/>
      <ellipse cx="400" cy="150" rx="240" ry="110" transform="rotate(-22 400 150)" fill="var(--navy)"/>
    </svg>
    <div class="brand">
      <span class="brand__name">Bramwell</span>
      <span class="brand__tagline">Financial Advisory Services Inc.</span>
    </div>
    <div class="contact">
      <p class="contact__name">MARCUS T. HALE</p>
      <p class="contact__role">CEO</p>
      <p class="contact__address">418 Harbor Street<br>Millbrook Falls, USA</p>
      <ul class="contact__lines">
        <li>
          <svg class="contact__icon" viewBox="0 0 14 14" aria-hidden="true">
            <circle cx="7" cy="7" r="7" fill="var(--gold)"/>
            <path d="M4.6 3.6l1.3 1.5-.7.9c.5 1 1.3 1.8 2.3 2.3l.9-.7 1.5 1.3-.8 1c-2.6-.3-4.9-2.6-5.2-5.2z" fill="var(--white)"/>
          </svg>
          1-555-014-2278
        </li>
        <li>
          <svg class="contact__icon" viewBox="0 0 14 14" aria-hidden="true">
            <circle cx="7" cy="7" r="7" fill="var(--gold)"/>
            <rect x="3.8" y="4.8" width="6.4" height="4.4" rx="0.6" fill="var(--white)"/>
            <path d="M3.9 5l3.1 2.3L10.1 5" stroke="var(--gold)" stroke-width="0.8" fill="none"/>
          </svg>
          mhale@bramwellfa.com
        </li>
      </ul>
    </div>
  </section>

  <section class="card card--back" aria-label="Business card back">
    <svg class="card__art" viewBox="0 0 478 280" aria-hidden="true">
      <rect width="478" height="280" fill="var(--navy)"/>
      <ellipse cx="125" cy="105" rx="250" ry="140" transform="rotate(-30 125 105)" fill="var(--gold)"/>
      <ellipse cx="100" cy="110" rx="220" ry="120" transform="rotate(-30 100 110)" fill="var(--white)"/>
    </svg>
    <div class="brand">
      <span class="brand__name">Bramwell</span>
      <span class="brand__tagline">Financial Advisory Services Inc.</span>
    </div>
    <p class="website">www.bramwellfa.com</p>
  </section>

</main>
</body>
</html>
```